VERDALIX " need somthing eye catching and envirnmental friendely materials

Business Card " UNIQUE..
- use the agreed on logo.
- use wooden background.
- the environmental sound should be HIGH.

Company slogan is ZERO DISCHARGE.
We work in deploying the latest technology “ USA & Europe” in the field of drill cutting recycle and economically managing the footprint.
With the ramp up in oil demands and the increase in oil prices , operators are extending their operations into new geographical areas “ government regulations and eco-sounds” created the need to a specialty services and products that should go parallel or even ahead.

Target Market(s)

OIL field and environmental concerned.
Mainly ENGINEERS.

Industry/Entity Type

Government

Font styles to use
Decorative
Script

Colors

Designer to choose colors to be used in the design.

Requirements
Must have
• Eco - sounded.

```html
<!DOCTYPE html>
<html lang="en">
<head>
<meta charset="UTF-8">
<title>VERDALIX Business Card</title>
<link rel="stylesheet" href="https://fonts.googleapis.com/css2?family=Cormorant+Garamond:wght@500;600&display=swap">
<style>
  :root {
    --page-bg: #ffffff;
    --wood-light: #e3bd86;
    --wood-mid: #cf9c5c;
    --wood-dark: #b27a3f;
    --card-white: #ffffff;
    --accent-orange: #e39a45;
    --text-grey: #5a5a5a;
    --brand-green: #3f7a2e;
    --faint-grey: #e6e4e0;
    --shadow: rgba(0, 0, 0, 0.28);
  }
  html, body {
    margin: 0;
    padding: 0;
    width: 1200px;
    height: 1052px;
    overflow: hidden;
    background: var(--page-bg);
    font-family: "Cormorant Garamond", Georgia, serif;
  }
  .canvas {
    position: relative;
    width: 1200px;
    height: 1052px;
  }
  .card {
    position: absolute;
    top: 381px;
    width: 520px;
    height: 290px;
    box-shadow: 3px 4px 8px var(--shadow);
    overflow: hidden;
  }
  .card--front { left: 60px; }
  .card--back {
    left: 620px;
    background: var(--card-white);
    border: 1px solid #e2e2e2;
    box-sizing: border-box;
  }
  .wood-surface {
    position: absolute;
    inset: 0;
    background:
      radial-gradient(ellipse at 30% 40%, rgba(255,235,200,0.35), transparent 60%),
      linear-gradient(100deg, var(--wood-light) 0%, var(--wood-mid) 45%, var(--wood-light) 70%, var(--wood-dark) 100%);
  }
  .brand {
    position: absolute;
    left: 0;
    right: 0;
    top: 50%;
    transform: translateY(-50%);
    display: flex;
    align-items: center;
    justify-content: center;
    gap: 14px;
  }
  .brand__dot {
    width: 34px;
    height: 34px;
    border-radius: 50%;
    background: var(--brand-green);
  }
  .brand__name {
    font-size: 44px;
    font-weight: 600;
    letter-spacing: 3px;
    color: var(--brand-green);
  }
  .brand--faint {
    left: -30px;
    right: auto;
    top: 62%;
  }
  .brand--faint .brand__dot {
    width: 150px;
    height: 150px;
    background: var(--faint-grey);
  }
  .contact-block {
    position: absolute;
    right: 26px;
    top: 38px;
    text-align: right;
  }
  .person__name {
    margin: 0;
    font-size: 25px;
    font-weight: 500;
    letter-spacing: 0.5px;
    color: var(--accent-orange);
  }
  .person__title {
    margin: 0;
    font-size: 20px;
    font-weight: 500;
    color: var(--text-grey);
  }
  .rule {
    width: 248px;
    height: 2px;
    margin: 6px 0 0 auto;
    background: var(--accent-orange);
  }
  .contact-list {
    list-style: none;
    margin: 40px 0 0;
    padding: 0;
    font-size: 18px;
    font-weight: 500;
    line-height: 1.15;
    color: var(--text-grey);
  }
</style>
</head>
<body>
<main class="canvas">
  <section class="card card--front">
    <div class="wood-surface" role="img" aria-label="Light natural wood grain texture"></div>
    <div class="brand">
      <span class="brand__dot"></span>
      <span class="brand__name">VERDALIX</span>
    </div>
  </section>

  <section class="card card--back">
    <div class="brand brand--faint" aria-hidden="true">
      <span class="brand__dot"></span>
    </div>
    <div class="contact-block">
      <h1 class="person__name">KARIM YOUSEF NADER</h1>
      <p class="person__title">Chief Executive Officer</p>
      <div class="rule"></div>
      <ul class="contact-list">
        <li>it@verdalix.com</li>
        <li>www.verdalix.ae</li>
        <li>cell&nbsp; 009715 555 214 38</li>
      </ul>
    </div>
  </section>
</main>
</body>
</html>
```